Company or website name
- The Steadfast Haulers and Storage
- Links to the website
- Pinecrestcartage.com
- Describe your company and organization and target audience
- Residential and commercial moving and relocation service that needs a website redesign.
- The design should have the following
- I NEED THE WEBSITE TO BE SIMPLE AND STRAIGHT TO THE POINT...MAIN CONCERN IS THAT THEY FILL OUT INFORMATION TO GET QUOTE. SITE EXAMPLE THAT I LIKE IS ( WWW.MYDORVALS.COM) https://www.corvellfreight.com/

```html
<!DOCTYPE html>
<html lang="en">
<head>
<meta charset="utf-8">
<title>Steadfast — Get a Free Moving Quote</title>
<link href="https://fonts.googleapis.com/css2?family=Roboto:ital,wght@0,400;0,500;0,700;1,400&family=Roboto+Condensed:wght@700&display=swap" rel="stylesheet">
<style>
  :root{
    --ink:#111111;
    --panel-dark:#2a2a2a;
    --hero-top:#3c3f44;
    --hero-bottom:#25272a;
    --form-bg:#f3f3f3;
    --strip:#ffffff;
    --field-border:#9a9a9a;
    --text:#222222;
    --white:#ffffff;
  }
  *{box-sizing:border-box;margin:0;padding:0}
  html,body{width:1200px;height:624px;overflow:hidden}
  body{position:relative;font-family:"Roboto",sans-serif;color:var(--text);background:var(--strip)}
  .abs{position:absolute}

  /* Hero side */
  .hero{left:0;top:0;width:676px;height:624px;background:linear-gradient(180deg,var(--hero-top) 0%,#4a4d52 45%,var(--hero-bottom) 100%)}
  .brand{left:75px;top:34px;display:flex;align-items:center;gap:8px;color:var(--white)}
  .brand-mark{width:16px;height:16px;background:var(--white)}
  .brand-name{font-family:"Roboto",sans-serif;font-weight:700;font-size:24px;letter-spacing:3px}
  .brand-tag{left:116px;top:71px;color:var(--white);font-size:7px;font-weight:700}
  .nav{top:53px;left:345px;display:flex;gap:0;color:var(--white);font-size:12.5px}
  .nav a{color:inherit;text-decoration:none;position:absolute;white-space:nowrap}
  .headline{left:167px;top:252px;width:342px;height:67px;border-top:1px solid var(--white);border-bottom:1px solid var(--white);color:var(--white);font-family:"Roboto Condensed",sans-serif;font-weight:700;font-size:68px;line-height:64px;text-align:center;letter-spacing:-0.5px}
  .thumb{top:478px;width:172px;height:107px;border:1px solid #cfcfcf;border-radius:2px}
  .t1{left:74px;background:linear-gradient(180deg,#cfd6dc 0%,#eaeaea 55%,#5c8a3a 100%)}
  .t2{left:252px;background:linear-gradient(90deg,#dfe6ea 0%,#f2f0ec 40%,#2b2f36 60%,#e6ded2 100%)}
  .t3{left:429px;background:linear-gradient(180deg,#9fb6c2 0%,#d2c3a4 60%,#b88a5a 100%)}
  .copy{left:74px;top:598px;color:var(--white);font-size:9px}

  /* Quote side */
  .form-bg{left:687px;top:0;width:513px;height:624px;background:var(--form-bg)}
  .call{left:700px;top:27px;display:flex;align-items:center;gap:5px;font-size:15px;font-weight:500;color:var(--ink)}
  .social{top:25px;display:flex;gap:5px;left:1047px}
  .social span{width:22px;height:22px;border:1.5px solid var(--ink);border-radius:50%}
  .quote-title{left:699px;top:62px;width:427px;height:43px;background:#000;color:var(--white);font-family:"Roboto Condensed",sans-serif;font-weight:700;font-size:25px;line-height:43px;padding-left:12px}
  .tab{top:119px;width:138px;height:93px;border:1px solid #dedede;background:var(--white);display:flex;flex-direction:column;align-items:center;justify-content:flex-end;padding-bottom:16px;font-weight:700;font-size:13.5px;color:var(--ink);gap:7px}
  .tab.active{background:var(--panel-dark);border-color:var(--panel-dark);color:var(--white)}
  .label{font-size:12px;color:var(--text)}
  .field{width:209px;height:40px;border:1px solid var(--field-border);border-radius:2px;background:var(--form-bg);font-size:11px;color:#333;padding:12px 13px}
  .hint{left:699px;top:391px;font-size:10.5px}
  .btn{top:509px;width:209px;height:40px;border-radius:2px;font-family:"Roboto Condensed",sans-serif;font-weight:700;font-size:17px;display:flex;align-items:center;justify-content:center}
  .btn-primary{left:700px;background:var(--panel-dark);color:var(--white)}
  .btn-outline{left:917px;border:2px solid var(--panel-dark);color:var(--ink);background:var(--form-bg)}
  .note{left:700px;width:426px;top:568px;text-align:center;font-style:italic;font-size:10.5px;color:#333}
</style>
</head>
<body>
  <section class="abs hero" role="img" aria-label="Dimmed photo of a branded moving truck on the road"></section>
  <div class="abs brand"><span class="brand-mark"></span><span class="brand-name">STEADFAST</span></div>
  <div class="abs brand-tag">the steadfast haulers &amp; storage inc.</div>
  <nav class="abs nav">
    <a style="left:0">SERVICES &#8964;</a>
    <a style="left:84px">FAQS</a>
    <a style="left:143px">BLOG</a>
    <a style="left:202px">CONTACT</a>
  </nav>
  <h1 class="abs headline">GET MOVED</h1>
  <div class="abs thumb t1" role="img" aria-label="Photo of a moving truck parked on a lawn"></div>
  <div class="abs thumb t2" role="img" aria-label="Photo of a mover in a branded shirt entering an office"></div>
  <div class="abs thumb t3" role="img" aria-label="Photo of a happy customer among moving boxes"></div>
  <div class="abs copy">© 2022 Steadfast</div>

  <div class="abs form-bg"></div>
  <div class="abs call">
    <svg width="22" height="22" viewBox="0 0 22 22"><circle cx="11" cy="11" r="10" fill="none" stroke="#111" stroke-width="1.5"/><path d="M7 6.5c.6-.6 1.3-.6 1.7 0l1 1.6c.3.5.2 1-.2 1.4l-.5.5c.6 1.3 1.6 2.3 2.9 2.9l.5-.5c.4-.4.9-.5 1.4-.2l1.6 1c.6.4.6 1.1 0 1.7l-.7.7c-.8.8-2.5.6-4.5-.9-1.6-1.2-2.9-2.6-3.8-4-1.2-1.8-1.3-3.4-.6-4.2z" fill="#111"/></svg>
    Call: 800.123.456.7890
  </div>
  <div class="abs social"><span></span><span></span><span></span></div>
  <h2 class="abs quote-title">GET A FREE MOVING QUOTE!</h2>

  <div class="abs tab active" style="left:700px">
    <svg width="34" height="32" viewBox="0 0 34 32" fill="none" stroke="#fff" stroke-width="1.6"><path d="M3 16 17 3l14 13"/><path d="M7 13v16h20V13"/><path d="M14 29v-9h6v9"/></svg>
    Residential</div>
  <div class="abs tab" style="left:844px">
    <svg width="38" height="32" viewBox="0 0 38 32" fill="none" stroke="#111" stroke-width="1.5"><rect x="2" y="3" width="18" height="28"/><rect x="20" y="12" width="16" height="19"/><path d="M6 8h3M13 8h3M6 14h3M13 14h3M6 20h3M13 20h3M24 17h3M30 17h3M24 23h3M30 23h3M2 3h14"/></svg>
    Office</div>
  <div class="abs tab" style="left:989px">
    <svg width="58" height="32" viewBox="0 0 58 32" fill="none" stroke="#111" stroke-width="1.4"><path d="M10 12 2 30h54l-8-16"/><circle cx="12" cy="10" r="6"/><circle cx="12" cy="10" r="2"/><path d="M12 16v6"/><circle cx="40" cy="6" r="4.5"/><path d="M40 10.5v5"/><path d="M14 22c8 0 10-6 26-6" stroke-dasharray="3 2"/></svg>
    Relocation</div>

  <label class="abs label" style="left:698px;top:235px">I am moving from... *</label>
  <label class="abs label" style="left:918px;top:235px">I am moving to...*</label>
  <div class="abs field" style="left:700px;top:260px">Zip Code</div>
  <div class="abs field" style="left:917px;top:260px">Zip Code</div>

  <label class="abs label" style="left:699px;top:320px">Moving Date*</label>
  <label class="abs label" style="left:918px;top:320px">Your Full Name (First and Last) *</label>
  <div class="abs field" style="left:700px;top:345px"></div>
  <div class="abs field" style="left:917px;top:345px"></div>
  <div class="abs hint">Date Format: MM slash DD slash YYYY</div>

  <label class="abs label" style="left:700px;top:429px">Your E-Mail Address *</label>
  <label class="abs label" style="left:920px;top:429px">Your Phone Number *</label>
  <div class="abs field" style="left:700px;top:454px"></div>
  <div class="abs field" style="left:917px;top:454px"></div>

  <div class="abs btn btn-primary">FREE QUOTE</div>
  <div class="abs btn btn-outline">MAKE A RESERVATION</div>
  <p class="abs note">A Marlowe Moving Solutions agent will be e-mailing you a quote in 24 hours or less</p>
</body>
</html>
```